Business Card Design Project

We are not a new company, but renamed to "Vantorin Kitchens" last year. We specialize in modern high-end cabinetry imports. We would like to communicate a sense of quality and cutting edge technology. Ideally the design would incorporate our logo colors, silver, red and preferably a black, matte background. Though we are open to suggestions.
Logo is attached.
Edit: I have attached rough drafts of the previous cards, this way you will have all necessary content that needs to go on the cards.
Updates
Project Deadline Extended
Reason: We have received a lot of great designs, but due to the sheer number we couldn't respond to all. We will extend the deadline for another 7 days to finalize and provide feedback to designers.
Thank you for your hard work!
Industry/Entity Type
Business
Look and feel
Each slider illustrates characteristics of the customer's brand and the style your logo design should communicate.

```html
<!DOCTYPE html>
<html lang="en">
<head>
<meta charset="utf-8">
<title>Vantorin Kitchens – Business Cards</title>
<link rel="stylesheet" href="https://fonts.googleapis.com/css2?family=Arimo:wght@400;700&family=PT+Sans&display=swap">
<style>
  :root {
    --stage: #e9e6e2;
    --label: #2a2a2a;
    --card-matte: #1a1b1c;
    --card-matte-edge: #0d0d0e;
    --card-gloss: #050505;
    --text: #ffffff;
    --silver: #c9c9cb;
    --silver-dark: #8f9092;
    --red: #e3242b;
    --divider: #5a5a5a;
  }
  * { margin: 0; padding: 0; box-sizing: border-box; }
  html, body { width: 1200px; height: 788px; overflow: hidden; }
  body {
    position: relative;
    background: var(--stage);
    font-family: "Arimo", Arial, sans-serif;
    color: var(--text);
  }
  .sheet-label {
    position: absolute;
    width: 200px;
    text-align: center;
    font-family: "PT Sans", sans-serif;
    font-size: 22px;
    color: var(--label);
  }
  .card {
    position: absolute;
    width: 525px;
    height: 300px;
    border-radius: 18px;
    overflow: hidden;
    box-shadow: 0 6px 14px rgba(0,0,0,0.35);
  }
  .card--matte {
    background: radial-gradient(ellipse at 50% 35%, #2b2c2e 0%, var(--card-matte) 55%, var(--card-matte-edge) 100%);
  }
  .card--gloss { background: var(--card-gloss); }
  .swoosh { position: absolute; width: 525px; height: 300px; left: 0; top: 0; }
  .brand {
    position: absolute;
    left: 0; right: 0;
    display: flex;
    align-items: center;
    justify-content: center;
    gap: 12px;
    font-weight: 700;
    font-size: 26px;
    letter-spacing: 2px;
    text-transform: uppercase;
    color: var(--silver);
  }
  .brand__square {
    width: 20px; height: 20px;
    background: var(--silver);
  }
  .brand--large { font-size: 30px; }
  .holder {
    position: absolute;
    top: 162px; left: 0; right: 0;
    text-align: center;
    font-size: 14px;
  }
  .holder__name { font-size: 17px; }
  .holder--bold .holder__name { font-weight: 700; }
  .contacts {
    position: absolute;
    top: 200px; left: 0; right: 0;
    display: flex;
    justify-content: center;
    font-size: 13.5px;
    line-height: 21px;
  }
  .contacts__col { padding: 2px 16px; }
  .contacts__col--left { text-align: right; border-right: 1px solid var(--divider); }
  .contacts b { font-weight: 700; }
  .address {
    position: absolute;
    top: 260px; left: 0; right: 0;
    text-align: center;
    font-size: 13.5px;
  }
  .texture {
    position: absolute;
    width: 240px; height: 110px;
  }
  .texture--top { left: 0; top: 0; background: radial-gradient(ellipse at 55% 10%, #4a4a4c 0%, #1c1c1d 55%, transparent 85%); }
  .texture--bottom { right: 0; bottom: 0; background: radial-gradient(ellipse at 45% 90%, #4a4a4c 0%, #1c1c1d 55%, transparent 85%); }
</style>
</head>
<body>
  <div class="sheet-label" style="left:207px;top:22px;">front</div>
  <div class="sheet-label" style="left:789px;top:22px;">front-1</div>
  <div class="sheet-label" style="left:214px;top:405px;">back</div>
  <div class="sheet-label" style="left:786px;top:405px;">Back - 1</div>

  <!-- front -->
  <section class="card card--matte" style="left:53px;top:70px;">
    <svg class="swoosh" viewBox="0 0 525 300" aria-hidden="true">
      <path d="M430 0 H525 V48 C505 22 470 6 430 0 Z" fill="var(--silver-dark)"/>
      <path d="M455 3 C485 10 510 25 525 42 V34 C505 18 482 8 455 3 Z" fill="var(--red)"/>
      <path d="M0 258 V300 H95 C60 292 25 278 0 258 Z" fill="var(--silver-dark)"/>
      <path d="M0 258 C25 276 55 288 80 294 C50 283 22 270 0 252 Z" fill="var(--red)"/>
    </svg>
    <div class="brand" style="top:100px;"><span class="brand__square"></span>Vantorin Kitchens</div>
    <div class="holder holder--bold"><span class="holder__name">MIREL DANKO,</span> President</div>
    <div class="contacts">
      <div class="contacts__col contacts__col--left"><b>phone</b> : 555.210.0144<br><b>cell</b> : 555.381.0926</div>
      <div class="contacts__col"><b>fax</b> : 555.210.0178<br>mirel@vantorinkitchens.ca</div>
    </div>
    <div class="address">1180 - 42 Ave., Northfield, AB T4R 2K9</div>
  </section>

  <!-- front-1 -->
  <section class="card card--gloss" style="left:630px;top:70px;">
    <svg class="swoosh" viewBox="0 0 525 300" aria-hidden="true">
      <path d="M430 0 H525 V48 C505 22 470 6 430 0 Z" fill="var(--silver-dark)"/>
      <path d="M455 3 C485 10 510 25 525 42 V34 C505 18 482 8 455 3 Z" fill="var(--red)"/>
      <path d="M0 258 V300 H95 C60 292 25 278 0 258 Z" fill="var(--silver-dark)"/>
      <path d="M0 258 C25 276 55 288 80 294 C50 283 22 270 0 252 Z" fill="var(--red)"/>
    </svg>
    <div class="brand" style="top:90px;"><span class="brand__square"></span>Vantorin Kitchens</div>
    <div class="holder" style="top:160px;"><span class="holder__name">OREN DANKO,</span> Director</div>
    <div class="contacts" style="top:194px;">
      <div class="contacts__col contacts__col--left"><b>phone</b> : 555.210.0144<br><b>cell</b> : 555.642.0315</div>
      <div class="contacts__col"><b>fax</b> : 555.210.0178<br>oren@vantorinkitchens.ca</div>
    </div>
    <div class="address" style="top:260px;">1180 - 42 Ave., Northfield, AB T4R 2K9</div>
  </section>

  <!-- back -->
  <section class="card card--matte" style="left:57px;top:446px;">
    <div class="brand brand--large" style="top:134px;"><span class="brand__square"></span>Vantorin Kitchens</div>
  </section>

  <!-- Back - 1 -->
  <section class="card card--gloss" style="left:624px;top:446px;">
    <div class="texture texture--top" role="img" aria-label="Perforated metal texture"></div>
    <div class="texture texture--bottom" role="img" aria-label="Perforated metal texture"></div>
    <div class="brand brand--large" style="top:134px;"><span class="brand__square"></span>Vantorin Kitchens</div>
  </section>
</body>
</html>
```